Business Cards for a law firm

Business cards for our law firm. Use our silhoette logo and OAK PARTNERS - check our website (www.oakpartners.example)

Contact Information for Business Card

our silhouette logo, OAK PARTNERS, 800-555-0147, Dorian Pemberton, dorian@oakpartners.example

Requirements
Must have
• our silhouette logo, OAK PARTNERS, 800-555-0147, Dorian Pemberton, dorian@oakpartners.example

```html
<!DOCTYPE html>
<html lang="en">
<head>
<meta charset="utf-8">
<title>Oak Partners — Business Card</title>
<link href="https://fonts.googleapis.com/css2?family=Fira+Sans:wght@400;600&display=swap" rel="stylesheet">
<style>
  :root {
    --navy: #22336b;
    --paper: #ffffff;
    --ink: #1e1e24;
    --backdrop: #2e2e2e;
  }
  html, body { margin: 0; padding: 0; overflow: hidden; }
  body {
    width: 1200px; height: 1059px;
    background: var(--backdrop);
    position: relative;
    font-family: "Fira Sans", sans-serif;
  }
  .card {
    position: absolute;
    box-shadow: 8px 14px 22px rgba(0,0,0,0.55);
  }
  .card-front {
    left: 256px; top: 100px; width: 688px; height: 391px;
    background: var(--paper);
  }
  .card-back {
    left: 253px; top: 537px; width: 694px; height: 394px;
    background: var(--navy);
    display: flex; align-items: center; justify-content: center;
  }
  .firm-name {
    position: absolute; left: 38px; top: 52px; margin: 0;
    font-size: 34px; font-weight: 600; letter-spacing: 2px;
    color: var(--navy);
  }
  .name-tab {
    position: absolute; left: 0; top: 143px; width: 18px; height: 41px;
    background: var(--navy); border-radius: 0 4px 4px 0;
  }
  .person-name {
    position: absolute; left: 38px; top: 138px; margin: 0;
    font-size: 25px; font-weight: 600; letter-spacing: 0.5px;
    color: var(--navy);
  }
  .person-role {
    position: absolute; left: 38px; top: 169px; margin: 0;
    font-size: 15.5px; letter-spacing: 0.5px; color: var(--ink);
  }
  .address {
    position: absolute; left: 38px; top: 215px; margin: 0;
    font-size: 16px; line-height: 20px; font-style: normal;
    letter-spacing: 0.4px; color: var(--ink);
  }
  .contact-list {
    position: absolute; left: 38px; top: 281px; margin: 0; padding: 0;
    list-style: none;
  }
  .contact-item {
    display: flex; align-items: center; height: 26px;
    font-size: 16px; letter-spacing: 0.4px; color: var(--ink);
  }
  .contact-icon { width: 13px; height: 13px; margin-right: 11px; fill: var(--navy); }
  .back-logo { display: flex; align-items: center; gap: 20px; }
  .back-logo-mark { width: 26px; height: 26px; background: var(--paper); }
  .back-logo-name {
    margin: 0; font-size: 44px; font-weight: 600; letter-spacing: 3px;
    color: var(--paper);
  }
</style>
</head>
<body>
  <section class="card card-front">
    <h1 class="firm-name">OAK PARTNERS</h1>
    <div class="name-tab"></div>
    <h2 class="person-name">DORIAN PEMBERTON</h2>
    <p class="person-role">OWNER</p>
    <address class="address">4120 Harbor View Ave #310,<br>Lakeside, CA 90000</address>
    <ul class="contact-list">
      <li class="contact-item">
        <svg class="contact-icon" viewBox="0 0 16 16"><path d="M3.5 1 6 1.4 7 5 5.3 6.4a9 9 0 0 0 4.3 4.3L11 9l3.6 1 .4 2.5-2 2C6.5 14.3 1.7 9.5 1.5 3z"/></svg>
        800-555-0147
      </li>
      <li class="contact-item">
        <svg class="contact-icon" viewBox="0 0 16 16"><path d="M1 3h14v10H1zm2 2v6h10V5l-5 4z" fill-rule="evenodd"/></svg>
        dorian@oakpartners.example
      </li>
      <li class="contact-item">
        <svg class="contact-icon" viewBox="0 0 16 16"><circle cx="8" cy="8" r="7"/><path d="M1 8h14M8 1c3 3 3 11 0 14M8 1c-3 3-3 11 0 14" stroke="#fff" stroke-width="1" fill="none"/></svg>
        www.oakpartners.example
      </li>
    </ul>
  </section>

  <section class="card card-back">
    <div class="back-logo">
      <span class="back-logo-mark"></span>
      <h1 class="back-logo-name">OAK PARTNERS</h1>
    </div>
  </section>
</body>
</html>
```